The quiet harbor with an elephant incorporated in the background

Target Market(s)

Real estate

Industry/Entity Type

Real Estate

Contact Information for Business Card

On back on want my name & number
In front I want the business name, "the quiet harbor", below to say staging & design

Logo Text

The quiet harbor

Font styles to use
Serif

Colors
000000

Requirements
Must have
• I want an elephant behind the writing in gold transperant

```html
<!DOCTYPE html>
<html lang="en">
<head>
<meta charset="utf-8">
<title>The Quiet Harbor — Business Card</title>
<link href="https://fonts.googleapis.com/css2?family=Marcellus+SC&family=Open+Sans:wght@400;700&family=Quicksand:wght@400&display=swap" rel="stylesheet">
<style>
  :root {
    --stage: #000000;
    --card: #feb402;
    --card-shade: #e9a300;
    --ink: #ffffff;
  }
  html, body {
    margin: 0;
    padding: 0;
    width: 1200px;
    height: 900px;
    overflow: hidden;
    background: var(--stage);
  }
  .canvas {
    position: relative;
    width: 1200px;
    height: 900px;
    background: var(--stage);
    color: var(--ink);
  }
  .card {
    position: absolute;
    top: 275px;
    width: 477px;
    height: 293px;
    background: var(--card);
    overflow: hidden;
  }
  .card--front {
    left: 116px;
    border-radius: 0 52px 0 52px;
  }
  .card--back {
    left: 622px;
    border-radius: 52px 0 52px 0;
  }
  .elephant-watermark {
    position: absolute;
    left: 18px;
    top: 2px;
    width: 440px;
    height: 291px;
    border-radius: 40px 40px 0 0;
    background: radial-gradient(ellipse 60% 70% at 50% 45%, var(--card-shade) 0%, rgba(233, 163, 0, 0.55) 60%, rgba(233, 163, 0, 0) 100%);
    opacity: 0.85;
  }
  .brand {
    position: absolute;
    text-align: center;
    z-index: 1;
  }
  .brand__name {
    font-family: "Marcellus SC", serif;
    white-space: nowrap;
    line-height: 1;
  }
  .brand__tagline {
    font-family: "Quicksand", sans-serif;
    white-space: nowrap;
    line-height: 1;
  }
  .card--front .brand {
    left: 27px;
    top: 64px;
    width: 234px;
  }
  .brand__square {
    display: block;
    width: 44px;
    height: 44px;
    margin: 0 auto 18px;
    background: var(--ink);
  }
  .card--front .brand__name {
    font-size: 23px;
  }
  .card--front .brand__tagline {
    font-size: 12px;
    margin-top: 2px;
  }
  .card--back .brand {
    left: 0;
    width: 477px;
    top: 208px;
  }
  .card--back .brand__name {
    font-size: 35px;
  }
  .card--back .brand__tagline {
    font-size: 17px;
    margin-top: 4px;
  }
  .contact {
    position: absolute;
    right: 20px;
    text-align: right;
    font-family: "Open Sans", sans-serif;
    font-size: 13px;
    line-height: 17px;
    white-space: nowrap;
  }
  .contact--person { top: 34px; }
  .contact__name {
    font-weight: 700;
    font-size: 19px;
    line-height: 22px;
  }
  .contact--address { top: 157px; }
  .contact--lines { top: 217px; }
  .contact__line {
    display: flex;
    justify-content: flex-end;
    align-items: center;
    gap: 7px;
  }
  .contact__icon {
    width: 10px;
    height: 10px;
    fill: none;
    stroke: var(--ink);
    stroke-width: 1.4;
  }
</style>
</head>
<body>
<main class="canvas">

  <section class="card card--front" aria-label="Card front">
    <div class="brand">
      <span class="brand__square"></span>
      <div class="brand__name">The Quiet Harbor</div>
      <div class="brand__tagline">staging &amp; design</div>
    </div>

    <div class="contact contact--person">
      <div class="contact__name">Marcus Ellery</div>
      <div class="contact__title">Managing Director</div>
    </div>

    <div class="contact contact--address">
      <div>48 Harbour Lane, Suite 2</div>
      <div>Bayview, 204815</div>
    </div>

    <div class="contact contact--lines">
      <div class="contact__line">044-278 391 605
        <svg class="contact__icon" viewBox="0 0 10 10"><path d="M2 1 L3.6 1 L4.2 3 L3.2 3.8 Q4.2 5.8 6.2 6.8 L7 5.8 L9 6.4 L9 8 Q9 9 8 9 Q1 8.5 1 2 Q1 1 2 1 Z" fill="#fff" stroke="none"/></svg>
      </div>
      <div class="contact__line">hello@quietharbor.co
        <svg class="contact__icon" viewBox="0 0 10 10"><rect x="0.5" y="2" width="9" height="6.5" fill="#fff" stroke="none"/><path d="M0.8 2.4 L5 5.6 L9.2 2.4" stroke="#feb402" stroke-width="1"/></svg>
      </div>
      <div class="contact__line">www.quietharbor.co
        <svg class="contact__icon" viewBox="0 0 10 10"><path d="M4.2 5.8 L5.8 4.2 M3.4 4.8 L2 6.2 Q1 7.2 2 8 Q2.8 9 3.8 8 L5.2 6.6 M4.8 3.4 L6.2 2 Q7.2 1 8 2 Q9 2.8 8 3.8 L6.6 5.2"/></svg>
      </div>
    </div>
  </section>

  <section class="card card--back" aria-label="Card back">
    <div class="elephant-watermark" role="img" aria-label="Transparent gold elephant illustration behind the business name"></div>
    <div class="brand">
      <div class="brand__name">The Quiet Harbor</div>
      <div class="brand__tagline">staging &amp; design</div>
    </div>
  </section>

</main>
</body>
</html>
```